Spiritual Healing bussiness needs logo/business card

Simple, clean looking logo/card
For spiritual business with healing services and occult rituals

Contact Information for Business Card

Needs my name: Tobin Varley
Business name: Lantern Healing Shop
Services provided and worded in this way:

Reiki Healing
Tarot
Oils
Rituals Of Change

Can look occult like but with light energy.

Colors
0255a3
3276b5
85abd2
33a6d7
85cae6
0292cd

```html
<!DOCTYPE html>
<html lang="en">
<head>
<meta charset="utf-8">
<title>Lantern Healing Shop – Business Card</title>
<link rel="stylesheet" href="https://fonts.googleapis.com/css2?family=Oswald:wght@500&family=Lato:wght@400;700&display=swap">
<style>
  :root {
    --stage: #2b2b2d;
    --card: #1c1d20;
    --card-edge: #26272b;
    --blue-deep: #0255a3;
    --blue-mid: #3276b5;
    --blue-bright: #0292cd;
    --grey-text: #a9abb0;
    --grey-rule: #5b5d62;
    --white: #f2f2f2;
    --pattern-tone: #222327;
  }
  * { margin: 0; padding: 0; box-sizing: border-box; }
  html, body { width: 1200px; height: 1108px; overflow: hidden; }
  body {
    background: var(--stage);
    display: flex;
    align-items: center;
    justify-content: center;
    gap: 60px;
    font-family: "Lato", sans-serif;
  }
  .card {
    width: 440px;
    height: 700px;
    background: var(--card);
    border-radius: 22px;
    border: 1px solid var(--card-edge);
    position: relative;
    overflow: hidden;
  }
  .card-front {
    display: flex;
    flex-direction: column;
    align-items: center;
    padding-top: 88px;
  }
  .brand-mark {
    width: 150px;
    height: 150px;
    border: 10px solid var(--blue-deep);
    border-radius: 50%;
  }
  .brand-name {
    margin-top: 26px;
    font-family: "Oswald", sans-serif;
    font-weight: 500;
    font-size: 40px;
    letter-spacing: 0.5px;
    color: var(--blue-bright);
    text-transform: uppercase;
    white-space: nowrap;
  }
  .tagline {
    margin-top: 4px;
    font-size: 15px;
    letter-spacing: 0.6px;
    color: var(--grey-text);
    text-transform: uppercase;
  }
  .person-name {
    margin-top: 90px;
    font-family: "Oswald", sans-serif;
    font-weight: 500;
    font-size: 30px;
    color: var(--blue-mid);
    text-transform: uppercase;
  }
  .contact-divider {
    margin-top: 18px;
    display: flex;
    align-items: center;
    gap: 8px;
    width: 340px;
  }
  .contact-divider .rule {
    flex: 1;
    height: 1px;
    background: var(--grey-rule);
  }
  .contact-divider svg { width: 26px; height: 26px; display: block; }
  .contact-list {
    margin-top: 14px;
    list-style: none;
    text-align: center;
    font-size: 19px;
    line-height: 1.45;
    color: var(--grey-text);
  }
  .card-back { display: flex; flex-direction: column; }
  .mark-pattern {
    flex: 1;
    background: linear-gradient(180deg, #26272b 0%, var(--pattern-tone) 70%, var(--card) 100%);
  }
  .services {
    height: 170px;
    display: flex;
    flex-direction: column;
    align-items: center;
    justify-content: center;
    gap: 10px;
    color: var(--white);
    font-size: 21px;
    letter-spacing: 0.4px;
    text-transform: uppercase;
  }
  .services .dot { margin: 0 12px; }
</style>
</head>
<body>
  <section class="card card-front">
    <div class="brand-mark" aria-hidden="true"></div>
    <h1 class="brand-name">Lantern Healing Shop</h1>
    <p class="tagline">Healing Services &amp; Occult Rituals</p>
    <h2 class="person-name">Tobin Varley</h2>
    <div class="contact-divider">
      <span class="rule"></span>
      <svg viewBox="0 0 26 26" aria-label="Phone"><circle cx="13" cy="13" r="13" fill="#0255a3"/><path d="M9 7c1 0 2 2.5 2 3s-1 1-1 1.5 2 4 4.5 4.5c.5 0 1-1 1.5-1s3 1 3 2-1.5 2-2.5 2C11 19 7 15 7 9.5 7 8 8 7 9 7z" fill="#1c1d20"/></svg>
      <svg viewBox="0 0 26 26" aria-label="Email"><circle cx="13" cy="13" r="13" fill="#0255a3"/><rect x="7" y="9" width="12" height="8" rx="1" fill="#1c1d20"/><path d="M7.5 9.5 13 14l5.5-4.5" stroke="#0255a3" stroke-width="1.2" fill="none"/></svg>
      <svg viewBox="0 0 26 26" aria-label="Website"><circle cx="13" cy="13" r="13" fill="#0255a3"/><circle cx="13" cy="13" r="6" fill="none" stroke="#1c1d20" stroke-width="1.6"/><path d="M7 13h12M13 7c-3 3-3 9 0 12M13 7c3 3 3 9 0 12" stroke="#1c1d20" stroke-width="1.3" fill="none"/></svg>
      <span class="rule"></span>
    </div>
    <ul class="contact-list">
      <li>044-987 650 214</li>
      <li>hello@lanternmail.com</li>
      <li>www.LanternHealingShop.com</li>
    </ul>
  </section>

  <section class="card card-back">
    <div class="mark-pattern" role="img" aria-label="Faint repeating brand mark pattern"></div>
    <div class="services">
      <p>Reiki Healing<span class="dot">•</span>Tarot</p>
      <p>Oils<span class="dot">•</span>Rituals of Change</p>
    </div>
  </section>
</body>
</html>
```